New website for gluNote

We are looking to redesign our e-newsletter gluNote. This a monthly newsletter that publishes the latest research and product news in the diabetes field for people with diabetes. Our current website is here: www.glunote.us.

The parameters are the new site must incorporate our logo, must use the same colors (variation in shade and adding some colors is fine, but the initial pallet should stay) and must be in 1024 by 768 px. It is crucially important that the font in the new design be easily readable (dark, well spaced). If it could be a layered PSD that would be ideal. We have attached 2 sketches of our own brainstorming for a potential lay-out for the home and a new issue page, but these are very rough and should not in any way limit the true designers out there.

We're envisioning a very polished, sophisticated looking magazine-esque site that presents a lot of information. When we were brainstorming for new site ideas we looked at major monthly publications such as the Harbor Monthly (www.harbormonthly.com) or Silver Quill (www.sq.com). Like these sites we would still like to feature much of our newest content on the front page, but in a manner that makes good use of space and feels uncluttered. Information needs to be clearly labeled and easy to find. In terms of the overall tone of the website, we do very much want it to be nice and elegant looking site, and one that is targeting a smart, engaged audience.
Updates

Reason: I didn't realize I'd made this due on a Sunday. Please take a couple of extra days everyone.

Industry/Entity Type

News

Requirements
Must have
• The logo. The same color scheme we currently use
Nice to have
• We like the idea of having a featured content box, of using hover buttons on top for our various sections, and potentially using a 3 column setup. However, we are not web designers, so the designer can use these suggestions at their discretion.

```html
<!DOCTYPE html>
<html lang="en">
<head>
<meta charset="utf-8">
<title>gluNote — Home</title>
<link rel="stylesheet" href="https://fonts.googleapis.com/css2?family=Arimo:wght@400;700&family=Tinos&display=swap">
<style>
:root{
  --frame:#4a2b20;
  --page:#ffffff;
  --brown:#3d2a22;
  --teal:#5cb0ab;
  --teal-dark:#3a908a;
  --teal-deep:#2b5f5c;
  --teal-pale:#d2ebe9;
  --orange:#e4561c;
  --grey-img:#c7c7c7;
  --side:#eeecea;
  --line:#d9d9d9;
}
*{box-sizing:border-box;margin:0;padding:0}
html,body{width:983px;height:1200px;overflow:hidden;background:var(--frame)}
body{font-family:Arimo,Arial,sans-serif;color:var(--brown)}
.stage{position:absolute;left:0;top:0;width:1024px;height:1250px;transform:scale(.96);transform-origin:0 0;
  background:radial-gradient(circle at 30% 20%,#55342a,var(--frame) 70%)}
.abs{position:absolute}
.page{left:22px;top:27px;width:980px;height:1185px;background:var(--page)}
.brand{left:55px;top:52px;font-size:64px;font-weight:400;color:var(--brown);letter-spacing:-1px;line-height:1}
.tagline{left:55px;top:131px;font-family:Tinos,'Times New Roman',serif;font-size:17px;color:var(--brown)}
.mail-icon{left:584px;top:77px}
.promo{left:655px;top:81px;font-size:18px;line-height:24px;color:var(--orange)}
.nav{left:23px;top:179px;width:978px;height:44px;background:linear-gradient(#7cc3be,#4fa6a0 50%,#3f9891);display:flex}
.nav a{display:flex;align-items:center;justify-content:center;height:44px;color:#fff;font-weight:700;font-size:12px;text-decoration:none;border-right:1px solid #2f7c77}
.nav a.active{background:linear-gradient(#3f7a77,#1f4f4c)}
.search{left:691px;top:185px;width:184px;height:30px;background:#fff;border-radius:14px;box-shadow:inset 0 1px 3px #999;font-size:11px;color:#2a4b4a;padding:10px 15px}
.search svg{position:absolute;right:8px;top:6px}
.adv{left:884px;top:185px;width:110px;height:30px;border-radius:12px;background:linear-gradient(#fff,#dcdcdc);font-size:11px;color:#444;text-align:center;line-height:30px}
.subnav{left:23px;top:223px;width:978px;height:37px;background:linear-gradient(#fff,#e3f2f1);border-bottom:1px solid #cfe1df;font-size:10.5px;color:#333}
.subnav span{position:absolute;top:14px}
.subnav i{position:absolute;left:104px;top:0;width:1px;height:37px;background:#d3e3e2}
.dropdown{left:128px;top:260px;width:198px;height:159px;background:#e6f4f3;box-shadow:0 2px 6px rgba(0,0,0,.3);padding:3px 1px;display:grid;grid-template-columns:90px 105px;gap:1px;grid-auto-rows:29px}
.dropdown span{background:var(--teal-pale);font-size:11px;color:#333;display:flex;align-items:center;padding-left:32px;border:1px solid #b9dcd9}
.sidebar{left:753px;top:260px;width:249px;height:952px;background:var(--side);box-shadow:inset 3px 0 4px -2px #bbb}
.feature{left:30px;top:284px;width:713px;height:257px;border:1px solid var(--line);border-radius:8px;background:linear-gradient(#fff 80%,#f2f2f2)}
.feature-img{left:36px;top:289px;width:429px;height:248px;border:1px solid #e4e4e4;border-radius:8px;background:#fff;color:#e3e3e3;font-size:24px;display:flex;align-items:center;justify-content:center}
.feature-text{left:486px;top:295px;width:235px}
h2{font-weight:400;font-size:20px;color:var(--brown)}
.body{font-size:12px;line-height:18px;color:#222}
.feature-text p{margin-top:12px}
.card{width:330px;height:162px}
.card .pic{position:absolute;left:0;top:0;width:155px;height:161px;background:var(--grey-img);border-radius:8px;color:#fff;font-size:18px;display:flex;align-items:center;justify-content:center}
.card h2{position:absolute;left:169px;top:-4px;white-space:nowrap}
.card .body{position:absolute;left:170px;top:30px;width:150px}
.card .more{position:absolute;right:16px;font-size:12px;font-weight:700;color:var(--orange)}
.join{left:763px;top:282px;width:230px;height:242px;background:radial-gradient(circle at 50% 15%,#7fc4bf,var(--teal) 60%)}
.join h3{position:absolute;top:24px;width:230px;text-align:center;font-weight:400;font-size:23px;line-height:30px;color:#fff;text-shadow:1px 1px 2px #2f6c68}
.join-btn{position:absolute;left:14px;top:113px;width:202px;height:118px;border:1px solid #d4eeec;border-radius:9px;background:linear-gradient(#2f7f7a,#4aa09a);color:#fff;font-size:17px;line-height:22px;text-align:center;padding-top:63px}
.join-btn svg{position:absolute;left:72px;top:8px}
.print{left:762px;top:541px;width:232px;height:124px;background:#fff;border:1px solid #b5b5b5}
.print p{position:absolute;left:10px;top:42px;width:125px;text-align:center;font-size:17px;line-height:24px;color:#444;text-shadow:1px 1px 1px #ccc}
.print svg{position:absolute;left:142px;top:11px}
.tabs{left:762px;top:682px;display:flex}
.tabs span{width:67px;height:41px;font-size:10px;line-height:13px;text-align:center;padding-top:8px;color:#eaf7f6;background:linear-gradient(#68bab5,#4ea49e);border-left:1px solid #fff}
.tabs span.on{background:#fff;color:#333;border:none}
.panel{left:762px;top:723px;width:232px;height:188px;background:#fff;padding:14px 12px 0 11px}
.panel h4{font-size:11px;font-weight:700;color:#222;padding-left:14px;position:relative}
.panel h4::before{content:"»";position:absolute;left:0;top:-2px;font-weight:400}
.panel .body{font-size:10.5px;padding:8px 0 14px 13px}
.panel .more{position:absolute;right:12px;top:165px;font-size:12px;font-weight:700;color:var(--orange)}
.sizes{left:825px;top:929px}
.footer{left:0;top:1226px;width:1024px;text-align:center;font-size:10px;color:#fff}
</style>
</head>
<body>
<div class="stage">
  <div class="abs page"></div>

  <header>
    <div class="abs brand">gluNote</div>
    <div class="abs tagline">research and product news for people with diabetes</div>
    <svg class="abs mail-icon" width="58" height="60" viewBox="0 0 58 60" aria-hidden="true">
      <defs><radialGradient id="orb" cx="40%" cy="30%" r="70%"><stop offset="0" stop-color="#6fd0ca"/><stop offset="1" stop-color="#1b7c78"/></radialGradient></defs>
      <ellipse cx="29" cy="56" rx="20" ry="3" fill="#ccc"/>
      <circle cx="29" cy="28" r="27" fill="url(#orb)"/>
      <rect x="15" y="19" width="28" height="19" rx="2" fill="#fff"/>
      <path d="M15 20 L29 31 L43 20" fill="none" stroke="#3a9a95" stroke-width="2"/>
    </svg>
    <div class="abs promo">A monthly newsletter for people eager to<br>learn more about managing their diabetes</div>
  </header>

  <nav class="abs nav">
    <a style="width:87px">Home</a>
    <a class="active" style="width:88px">Issues</a>
    <a style="width:99px">Columns</a>
    <a style="width:85px">Topics</a>
    <a style="width:96px">About Us</a>
  </nav>
  <div class="abs search">Search
    <svg width="18" height="18" viewBox="0 0 18 18" aria-hidden="true"><circle cx="7" cy="7" r="5" fill="none" stroke="#555" stroke-width="2"/><path d="M11 11 L16 16" stroke="#555" stroke-width="3"/></svg>
  </div>
  <div class="abs adv">Advanced Search</div>

  <div class="abs subnav"><span style="left:13px">CURRENT ISSUE</span><i></i><span style="left:116px">ARCHIVES</span></div>

  <aside class="abs sidebar"></aside>

  <section class="abs feature"></section>
  <div class="abs feature-img" role="img" aria-label="Featured story image">FEATURED IMAGE</div>
  <div class="abs feature-text">
    <h2>Featured Content</h2>
    <p class="body">Lorem ipsum dolor siit amet consecutor. Lorem ipsum dolor siit amet consecutor. Lorem ipsum dolor siit amet consecutor. Lorem ipsum dolor siit amet consecutor.</p>
    <p class="body">Lorem ipsum dolor siit amet consecutor. Lorem ipsum dolor siit amet consecutor. Lorem ipsum dolor siit amet consecutor. Lorem ipsum dolor siit amet consecutor.</p>
  </div>

  <div class="abs dropdown">
    <span>2011</span><span>January</span>
    <span>2010</span><span>February</span>
    <span>2009</span><span>March</span>
    <span>2008</span><span>April</span>
    <span>2007</span><span>May</span>
  </div>

  <article class="abs card" style="left:43px;top:574px"><div class="pic" role="img" aria-label="Column image">Image</div><h2>From the Editor</h2><p class="body">Lorem ipsum dolor siit amet consecutor. Lorem ipsum dolor siit amet consecutor. Lorem ipsum dolor siit amet consecutor.</p><span class="more" style="top:128px">Read More...</span></article>
  <article class="abs card" style="left:414px;top:574px"><div class="pic" role="img" aria-label="Column image">Image</div><h2>Learning Curve</h2><p class="body">Lorem ipsum dolor siit amet consecutor. Lorem ipsum dolor siit amet consecutor. Lorem ipsum dolor siit amet consecutor.</p><span class="more" style="top:128px">Read More...</span></article>
  <article class="abs card" style="left:43px;top:789px"><div class="pic" role="img" aria-label="Column image">Image</div><h2>Sum Musings</h2><p class="body">Lorem ipsum dolor siit amet consecutor. Lorem ipsum dolor siit amet consecutor. Lorem ipsum dolor siit amet consecutor.</p><span class="more" style="top:128px">Read More...</span></article>
  <article class="abs card" style="left:414px;top:789px"><div class="pic" role="img" aria-label="Column image">Image</div><h2>Trial Watch</h2><p class="body" style="top:47px">Lorem ipsum dolor siit amet consecutor. Lorem ipsum dolor siit amet consecutor. Lorem ipsum dolor siit amet consecutor.</p><span class="more" style="top:145px">Read More...</span></article>
  <article class="abs card" style="left:43px;top:1005px"><div class="pic" role="img" aria-label="Column image">Image</div><h2>Quotable Quotes</h2><p class="body">Lorem ipsum dolor siit amet consecutor. Lorem ipsum dolor siit amet consecutor. Lorem ipsum dolor siit amet consecutor.</p><span class="more" style="top:128px">Read More...</span></article>
  <article class="abs card" style="left:414px;top:1005px"><div class="pic" role="img" aria-label="Column image">Image</div><h2>Finger Sticks</h2><p class="body">Lorem ipsum dolor siit amet consecutor. Lorem ipsum dolor siit amet consecutor. Lorem ipsum dolor siit amet consecutor.</p><span class="more" style="top:128px">Read More...</span></article>

  <div class="abs join">
    <h3>Join the gluNote<br>community!</h3>
    <div class="join-btn">
      <svg width="58" height="50" viewBox="0 0 58 50" aria-hidden="true"><rect x="2" y="6" width="48" height="38" rx="3" fill="#f4f4f4" stroke="#9ab" /><rect x="2" y="6" width="48" height="8" fill="#3a7fc2"/><rect x="8" y="19" width="12" height="14" fill="#9cc3e6"/><path d="M25 21h18M25 27h18M8 38h34" stroke="#999" stroke-width="2"/></svg>
      Sign up for a free<br>subscription here
    </div>
  </div>

  <div class="abs print">
    <p>Print our latest issue here</p>
    <svg width="82" height="102" viewBox="0 0 82 102" aria-hidden="true"><path d="M2 2 H60 L80 22 V100 H2 Z" fill="#fafafa" stroke="#ccc"/><path d="M60 2 V22 H80" fill="#e6e6e6" stroke="#ccc"/><rect x="2" y="78" width="78" height="20" fill="#d8231a"/></svg>
  </div>

  <div class="abs tabs"><span class="on">Recently<br>Added</span><span>Most<br>Popular</span><span>Editors<br>Picks</span></div>
  <div class="abs panel">
    <h4>Article 1</h4>
    <p class="body">Lorem ipsum dolor siit amet consecutor. Lorem ipsum dolor siit amet dolor.</p>
    <h4>Article 2</h4>
    <p class="body">Lorem ipsum dolor siit amet consecutor. Lorem ipsum dolor siit amet dolor.</p>
    <span class="more">More...</span>
  </div>

  <svg class="abs sizes" width="94" height="43" viewBox="0 0 94 43" aria-label="Text size controls">
    <defs><linearGradient id="key" x1="0" y1="0" x2="0" y2="1"><stop offset="0" stop-color="#fafafa"/><stop offset="1" stop-color="#cfcfcf"/></linearGradient></defs>
    <rect x="1" y="1" width="40" height="40" rx="4" fill="url(#key)" stroke="#777"/>
    <rect x="52" y="1" width="40" height="40" rx="4" fill="url(#key)" stroke="#777"/>
    <g font-family="Arimo,Arial,sans-serif" fill="#555">
      <path d="M6 16 L10 10 L14 16 Z"/><text x="5" y="36" font-size="12">A</text><text x="17" y="36" font-size="26">A</text>
      <path d="M83 12 L87 18 L91 12 Z" transform="translate(-4 0)"/><text x="56" y="36" font-size="26">A</text><text x="76" y="36" font-size="12">A</text>
    </g>
  </svg>

  <footer class="abs footer">© 2011 gluNote®. All rights reserved.</footer>
</div>
</body>
</html>
```